Redesign Of Current Landing Page

I need to redesign this landing page https://www.brightlanepromo.biz/?page=landing&landing=23 (Please do not opt in because when you do it will show you the home page. Please clear your cookies before going to this url above to view the 1 page landing page.)

Please use my updated website as a reference for colors and logo.
http://sitecradlewerk.com/dh/bpq/index.html

I would like the call to action to be a button that opens into a lead form...

Button would be "Download Samples"

Target Market(s)

small business owners

Industry/Entity Type

Marketing

Number of Pages Required

1 page

Colors

Designer to choose colors to be used in the design.

Requirements
Must have
• must be full responsive on all devices
Nice to have
• must have a legitimate professional apeal to it
Should not have
• open

```html
<!DOCTYPE html>
<html lang="en">
<head>
<meta charset="utf-8">
<title>Brightlane Promo Group – Promotional Incentives</title>
<link rel="stylesheet" href="https://fonts.googleapis.com/css2?family=Lato:wght@400;700&family=Open+Sans:ital,wght@0,400;0,600;1,400;1,600&display=swap">
<style>
:root{
  --blue:#0a6fc8;
  --blue-head:#1769b3;
  --dark:#3d3d3d;
  --footer:#454545;
  --ink:#333333;
  --white:#ffffff;
  --ring:#d9d9d9;
}
*{margin:0;padding:0;box-sizing:border-box}
html,body{width:1200px;height:2166px;overflow:hidden}
body{position:relative;background:var(--white);font-family:"Open Sans",Arial,sans-serif;color:var(--ink)}
.abs{position:absolute}

/* header */
.site-header{left:0;top:0;width:1200px;height:105px;background:var(--white)}
.brand{left:100px;top:34px;display:flex;align-items:center;gap:10px}
.brand-dot{width:34px;height:34px;border-radius:50%;background:var(--blue)}
.brand-name{font-family:"Lato",sans-serif;font-weight:700;font-size:30px;color:#222;letter-spacing:1px}
.main-nav{right:98px;top:44px;display:flex;gap:44px;font-size:15px}
.main-nav a{color:#222;text-decoration:none}
.main-nav a.active{color:var(--blue)}

/* hero */
.hero{left:0;top:105px;width:1200px;height:492px;overflow:hidden}
.hero-photo{width:100%;height:100%;background:linear-gradient(100deg,#2b2420 0%,#4a3a32 30%,#6e5a52 55%,#b89a8c 80%,#d8c2b4 100%)}
.hero-shade{left:0;top:0;width:100%;height:100%;background:linear-gradient(90deg,rgba(0,0,0,0.1) 40%,rgba(0,0,0,0.35) 100%)}
.hero-copy{left:694px;top:80px;width:405px;color:var(--white)}
.hero-title{font-family:"Lato",sans-serif;font-weight:700;font-size:37px;line-height:49px}
.hero-text{margin-top:24px;font-size:13.5px;line-height:22px;font-weight:600;text-align:justify}
.btn-samples{display:inline-block;margin-top:27px;width:166px;height:47px;line-height:47px;text-align:center;background:var(--blue);color:var(--white);font-size:14.5px;font-weight:600;border-radius:3px;box-shadow:0 2px 0 rgba(255,255,255,.5)}
.hero-arrow{top:220px}

/* reasons */
.section-title{left:0;width:1200px;text-align:center;font-family:"Lato",sans-serif;font-weight:700;font-size:28px;color:var(--blue-head)}
.title-rule{height:2px;background:var(--blue-head)}
.reason{top:797px;width:180px;text-align:center;font-size:13px;line-height:23px;font-weight:600;color:#333;white-space:nowrap}
.reason-icon{display:block;margin:0 auto 14px;width:120px;height:120px}

/* split section */
.split{left:0;top:1025px;width:1200px;height:562px}
.split-heading{font-family:"Lato",sans-serif;font-weight:700;font-size:26px;color:var(--white)}
.split-rule{height:2px;background:var(--white)}
.point-list{list-style:none;width:468px;color:var(--white);font-size:13.5px;line-height:22.5px}
.point-list li{position:relative;padding-left:27px;margin-bottom:15px;text-align:justify}
.point-list li svg{position:absolute;left:0;top:4px}

/* testimonial */
.quote{left:128px;top:1727px;width:944px;text-align:center;font-style:italic;font-weight:600;font-size:14px;line-height:26px;color:#444}
.quote-author{left:0;top:1877px;width:1200px;text-align:center;color:var(--blue-head);font-weight:600;font-size:17px}

/* footer */
.site-footer{left:0;top:1963px;width:1200px;height:203px;background:var(--footer);color:var(--white)}
.footer-nav{left:0;top:61px;width:1200px;text-align:center;font-size:15px;font-weight:600;word-spacing:2px}
.footer-nav span{margin:0 22px}
.footer-rule{left:98px;top:120px;width:1004px;height:1px;background:#8a8a8a}
.copyright{left:0;top:150px;width:1200px;text-align:center;font-size:13px;font-weight:600}
</style>
</head>
<body>

<header class="site-header abs">
  <div class="brand abs"><span class="brand-dot"></span><span class="brand-name">BLPG</span></div>
  <nav class="main-nav abs">
    <a class="active" href="#">HOME</a><a href="#">ABOUT US</a><a href="#">SERVICES</a><a href="#">TESTIMONIALS</a><a href="#">CONTACT US</a>
  </nav>
</header>

<section class="hero abs">
  <div class="hero-photo" role="img" aria-label="Blurred photo of a hand holding a smartphone surrounded by glowing digital marketing icons"></div>
  <div class="hero-shade abs"></div>
  <svg class="hero-arrow abs" style="left:32px" width="32" height="60" viewBox="0 0 32 60"><polyline points="30,2 2,30 30,58" fill="none" stroke="#fff" stroke-width="2"/></svg>
  <svg class="hero-arrow abs" style="left:1134px" width="32" height="60" viewBox="0 0 32 60"><polyline points="2,2 30,30 2,58" fill="none" stroke="#fff" stroke-width="2"/></svg>
  <div class="hero-copy abs">
    <h1 class="hero-title">Brightlane Promo<br>Incentives</h1>
    <p class="hero-text">Brightlane Promo Group, Inc. provides high perceived value promotional incentives to businesses.</p>
    <a class="btn-samples">Download Samples</a>
  </div>
</section>

<h2 class="section-title abs" style="top:664px">Why Offer Incentives To Customers?</h2>
<div class="title-rule abs" style="left:545px;top:724px;width:110px"></div>

<div class="reason abs" style="left:90px">
  <svg class="reason-icon" viewBox="0 0 120 120"><circle cx="60" cy="60" r="58" fill="var(--ring)"/><circle cx="60" cy="60" r="54" fill="var(--blue)"/>
    <g fill="#fff"><rect x="33" y="66" width="8" height="16"/><rect x="46" y="58" width="8" height="24"/><rect x="59" y="50" width="8" height="32"/><rect x="72" y="42" width="8" height="40"/></g>
    <polyline points="32,58 48,44 58,50 80,30" fill="none" stroke="#fff" stroke-width="4"/><polygon points="84,26 72,28 82,38" fill="#fff"/></svg>
  Increase Responses From<br>Your Existing Ads
</div>
<div class="reason abs" style="left:275px">
  <svg class="reason-icon" viewBox="0 0 120 120"><circle cx="60" cy="60" r="58" fill="var(--ring)"/><circle cx="60" cy="60" r="54" fill="var(--dark)"/>
    <g fill="#fff"><path d="M64 30a10 10 0 0 0-3 13l-12 12 5 5 12-12a10 10 0 0 0 13-3l-6-1-2-6 4-5a10 10 0 0 0-11-3z"/><path d="M30 72h12l10 4h14a4 4 0 0 1 0 8H52v2h16l16-10a4 4 0 0 1 5 6L70 94H30z"/></g></svg>
  #1 Sales Closing Tool -<br>Gift w/ Purchase
</div>
<div class="reason abs" style="left:451px">
  <svg class="reason-icon" viewBox="0 0 120 120"><circle cx="60" cy="60" r="58" fill="var(--ring)"/><circle cx="60" cy="60" r="54" fill="var(--blue)"/>
    <g fill="#fff"><circle cx="60" cy="46" r="15"/><path d="M30 72h12l10 4h14a4 4 0 0 1 0 8H52v2h16l16-10a4 4 0 0 1 5 6L70 94H30z"/></g>
    <polyline points="53,46 58,51 67,41" fill="none" stroke="var(--blue)" stroke-width="3"/></svg>
  Build Brand Awareness<br>and Trust
</div>
<div class="reason abs" style="left:625px">
  <svg class="reason-icon" viewBox="0 0 120 120"><circle cx="60" cy="60" r="58" fill="var(--ring)"/><circle cx="60" cy="60" r="54" fill="var(--dark)"/>
    <g stroke="#fff" stroke-width="3"><line x1="60" y1="54" x2="60" y2="80"/><line x1="34" y1="62" x2="86" y2="62"/><line x1="42" y1="78" x2="78" y2="78"/></g>
    <g fill="#fff"><circle cx="60" cy="42" r="9"/><circle cx="60" cy="62" r="8"/><circle cx="34" cy="62" r="5"/><circle cx="86" cy="62" r="5"/><circle cx="42" cy="78" r="5"/><circle cx="78" cy="78" r="5"/><circle cx="60" cy="84" r="5"/></g></svg>
  Insure The Sale Over<br>Your Competition
</div>
<div class="reason abs" style="left:795px">
  <svg class="reason-icon" viewBox="0 0 120 120"><circle cx="60" cy="60" r="58" fill="var(--ring)"/><circle cx="60" cy="60" r="54" fill="var(--blue)"/>
    <g fill="none" stroke="#fff" stroke-width="5"><path d="M38 62v-8a8 8 0 0 1 8-8h30"/><path d="M82 58v8a8 8 0 0 1-8 8H44"/></g>
    <g fill="#fff"><polygon points="72,38 84,46 72,54"/><polygon points="48,66 36,74 48,82"/></g></svg>
  Boost Repeat &amp;<br>Referral Business
</div>
<div class="reason abs" style="left:950px">
  <svg class="reason-icon" viewBox="0 0 120 120"><circle cx="60" cy="60" r="58" fill="var(--ring)"/><circle cx="60" cy="60" r="54" fill="var(--dark)"/>
    <circle cx="60" cy="60" r="24" fill="none" stroke="#fff" stroke-width="4"/>
    <text x="60" y="71" text-anchor="middle" font-family="Lato,sans-serif" font-weight="700" font-size="30" fill="#fff">$</text></svg>
  Improve Retention<br>Rates
</div>

<section class="split abs">
  <svg class="abs" style="left:0;top:0" width="1200" height="562" viewBox="0 0 1200 562">
    <polygon points="0,0 600,68 600,494 0,562" fill="var(--blue)"/>
    <polygon points="600,68 1200,0 1200,562 600,494" fill="var(--dark)"/>
  </svg>
  <h3 class="split-heading abs" style="left:98px;top:112px">Imagine</h3>
  <div class="split-rule abs" style="left:98px;top:160px;width:72px"></div>
  <ul class="point-list abs" style="left:98px;top:198px">
    <li><svg width="18" height="13" viewBox="0 0 18 13"><path d="M1 6h4l4-5 2 1-1 3h6a1 1 0 0 1 0 3h-5v4H5V7" fill="none" stroke="#fff" stroke-width="1.4"/></svg>Being able to create exciting give away promotions that will boost your sales without ever having to worry about cost.</li>
    <li><svg width="18" height="13" viewBox="0 0 18 13"><path d="M1 6h4l4-5 2 1-1 3h6a1 1 0 0 1 0 3h-5v4H5V7" fill="none" stroke="#fff" stroke-width="1.4"/></svg>Brightlane Promo Group, Inc. provides high-perceived value promotional incentives to businesses that want to advertise an exciting Give Away that will instantly attract more customers from your existing advertising efforts.</li>
    <li><svg width="18" height="13" viewBox="0 0 18 13"><path d="M1 6h4l4-5 2 1-1 3h6a1 1 0 0 1 0 3h-5v4H5V7" fill="none" stroke="#fff" stroke-width="1.4"/></svg>Your business can give away incentive certificates that are redeemable for luxury hotel &amp; resort stays with airfare included, cruises, cash for gas, groceries, dining and even electronic goods.</li>
  </ul>
  <h3 class="split-heading abs" style="left:634px;top:112px">How Can We Do It?</h3>
  <div class="split-rule abs" style="left:634px;top:160px;width:130px"></div>
  <ul class="point-list abs" style="left:634px;top:198px">
    <li><svg width="18" height="13" viewBox="0 0 18 13"><path d="M1 6h4l4-5 2 1-1 3h6a1 1 0 0 1 0 3h-5v4H5V7" fill="none" stroke="#fff" stroke-width="1.4"/></svg>We help fill empty rooms for thousands of hotels and resorts in hundreds of destinations around the world as well as the major cruise lines. Hotels and resorts are rarely full so when we place someone in their empty rooms, they end up making it up when travelers spend money on room service, spa services, eat at their in-house restaurants, casino and take advantage of other amenities that drive revenue.</li>
    <li><svg width="18" height="13" viewBox="0 0 18 13"><path d="M1 6h4l4-5 2 1-1 3h6a1 1 0 0 1 0 3h-5v4H5V7" fill="none" stroke="#fff" stroke-width="1.4"/></svg>We also help over 18,000 restaurants, electronic manufacturers, the major gas companies and top grocery chains in the U.S and Canada increase brand awareness as well as increase customer loyalty.</li>
  </ul>
</section>

<h2 class="section-title abs" style="top:1602px">Our Testimonials</h2>
<div class="title-rule abs" style="left:555px;top:1659px;width:90px"></div>
<svg class="abs" style="left:100px;top:1685px" width="28" height="22" viewBox="0 0 28 22"><g fill="var(--blue)"><path d="M0 12C0 5 4 1 10 0l1 3C7 4 5 7 5 10h6v12H0z"/><path d="M16 12C16 5 20 1 26 0l1 3c-4 1-6 4-6 7h6v12H16z"/></g></svg>
<p class="quote abs">I began using your incentives two years ago to boost lead generation efforts. I have experienced a 63% increase in lead captures. And, even more importantly, my sales have increased as well. The ability to offer unlimited certificates and not having to pay for each certificate I give away is perhaps the best feature of the program, but having the flexibility to email or print certificates for my customers is also wonderful. I even use your html banners to automate my promotions right on my website!,</p>
<svg class="abs" style="left:1074px;top:1838px" width="28" height="22" viewBox="0 0 28 22"><g fill="var(--blue)" transform="rotate(180 14 11)"><path d="M0 12C0 5 4 1 10 0l1 3C7 4 5 7 5 10h6v12H0z"/><path d="M16 12C16 5 20 1 26 0l1 3c-4 1-6 4-6 7h6v12H16z"/></g></svg>
<p class="quote-author abs">- Dana R. Maple Ridge, TN</p>

<footer class="site-footer abs">
  <nav class="footer-nav abs">HOME<span>|</span>ABOUT US<span>|</span>SERVICES<span>|</span>TESTIMONIALS<span>|</span>CONTACT US</nav>
  <div class="footer-rule abs"></div>
  <p class="copyright abs">© 2017 Brightlane Promo Group, Inc. - All Rights Reserved</p>
</footer>

</body>
</html>
```